Awesome photographers card for an awesome new business

Double sided business card Black background and silver logo in middle on one side. Details on otherside. please keep it simple

Industry/Entity Type

Photographer

Contact Information for Business Card

Gerald Fenwick
0452817360
GeraldFenwickPhotography47@mailbox.test
www.GeraldFenwickPhotography.test.au
Instagram _Gerald_fenwick

Requirements
Must have
• My logo in Silver
• please use instagram logo instead of "Instagram"

```html
<!DOCTYPE html>
<html lang="en">
<head>
<meta charset="UTF-8">
<title>Gerald Fenwick Photography – Business Card</title>
<link rel="stylesheet" href="https://fonts.googleapis.com/css2?family=Roboto+Condensed:wght@400;700&display=swap">
<style>
  :root {
    --canvas: #e9e7e4;
    --card-white: #fbfbfb;
    --card-black: #1d1d1d;
    --silver-light: #d9d9d9;
    --silver-mid: #a8a8a8;
    --silver-dark: #7d7d7d;
    --ink-grey: #5a5a5a;
    --text-white: #ffffff;
    --logo-silver: #c9c9c9;
  }
  * { margin: 0; padding: 0; box-sizing: border-box; }
  html, body { width: 1200px; height: 911px; overflow: hidden; }
  body {
    background: var(--canvas);
    font-family: "Roboto Condensed", Arial, sans-serif;
    position: relative;
  }
  .card {
    position: absolute;
    width: 540px;
    height: 310px;
    border-radius: 18px;
    overflow: hidden;
    box-shadow: 0 10px 28px rgba(0,0,0,0.25);
  }
  .card--front { left: 45px; top: 300px; background: var(--card-white); }
  .card--back { left: 615px; top: 300px; background: var(--card-black); }

  .card__swoosh { position: absolute; inset: 0; width: 100%; height: 100%; }

  .card__name {
    position: absolute;
    right: 36px;
    top: 34px;
    font-weight: 700;
    font-size: 22px;
    letter-spacing: 0.5px;
    text-transform: uppercase;
    color: var(--ink-grey);
  }

  .brand-mark {
    position: absolute;
    display: flex;
    align-items: center;
    justify-content: center;
    border-radius: 50%;
    text-align: center;
    font-weight: 400;
  }
  .brand-mark--front {
    left: 40px; top: 70px;
    width: 120px; height: 120px;
    border: 2px solid var(--silver-mid);
    color: var(--silver-dark);
    font-size: 17px;
    line-height: 1.2;
  }
  .brand-mark--back {
    left: 185px; top: 70px;
    width: 170px; height: 170px;
    border: 3px solid var(--logo-silver);
    color: var(--logo-silver);
    font-size: 24px;
    line-height: 1.2;
  }

  .contact-list {
    position: absolute;
    left: 215px;
    top: 196px;
    list-style: none;
    color: var(--text-white);
    font-size: 15px;
    line-height: 23px;
  }
  .contact-list li { display: flex; align-items: center; gap: 10px; }
  .contact-list svg { width: 13px; height: 13px; flex: none; }
</style>
</head>
<body>

<section class="card card--front" aria-label="Business card front">
  <svg class="card__swoosh" viewBox="0 0 540 310" preserveAspectRatio="none" aria-hidden="true">
    <defs>
      <linearGradient id="silverBand" x1="0" y1="1" x2="1" y2="0">
        <stop offset="0" stop-color="#8a8a8a"/>
        <stop offset="0.55" stop-color="#a9a9a9"/>
        <stop offset="1" stop-color="#cfcfcf"/>
      </linearGradient>
    </defs>
    <path d="M150 310 C 240 200, 380 150, 540 118 L540 310 Z" fill="#e2e2e2"/>
    <path d="M168 310 C 255 212, 390 162, 540 132 L540 310 Z" fill="url(#silverBand)"/>
  </svg>

  <div class="card__name">Gerald Fenwick</div>

  <div class="brand-mark brand-mark--front">Gerald<br>Fenwick</div>

  <ul class="contact-list">
    <li>
      <svg viewBox="0 0 16 16"><path fill="#fff" d="M3.6 1.5l2.3 2.6-1.3 1.8c.9 2 2.5 3.6 4.5 4.5l1.8-1.3 2.6 2.3-1.2 2.1C7 13.3 2.7 9 2.5 3.6z"/></svg>
      0452817360
    </li>
    <li>
      <svg viewBox="0 0 16 16"><rect x="1.5" y="3.5" width="13" height="9" fill="none" stroke="#fff" stroke-width="1.5"/><path d="M1.5 3.5L8 9l6.5-5.5" fill="none" stroke="#fff" stroke-width="1.5"/></svg>
      GeraldFenwickPhotography47@mailbox.test
    </li>
    <li>
      <svg viewBox="0 0 16 16"><circle cx="8" cy="8" r="6.5" fill="none" stroke="#fff" stroke-width="1.5"/><path d="M1.5 8h13M8 1.5c-3 3.5-3 9.5 0 13M8 1.5c3 3.5 3 9.5 0 13" fill="none" stroke="#fff" stroke-width="1.2"/></svg>
      www.GeraldFenwickPhotography.test.au
    </li>
    <li>
      <svg viewBox="0 0 16 16"><rect x="2" y="2" width="12" height="12" fill="#fff"/></svg>
      _Gerald_fenwick
    </li>
  </ul>
</section>

<section class="card card--back" aria-label="Business card back">
  <div class="brand-mark brand-mark--back">Gerald<br>Fenwick</div>
</section>

</body>
</html>
```